IT Support Business needs a Flyer Designed

Have just had new logo and business cards made for new business called Byte Harbor, am now in need of a new flyer design. Byte Harbor will be providing home and small business it support.
Updates
Byte Harbor flyer design brief has been uploaded. The contest has also been changed to payment guaranteed.
If you need anymore information please feel free to contact myself.
Project Deadline Extended
Reason: I signed up early to take advantage of the artfolly 24 hour sale, and was a few days late in providing a design brief. Therefore I am extending the deadline by 2 days, to ensure it lasts for a good 2 weeks.
Have worked on and refined the Design Brief a bit more, hoping it makes it a bit clearer as to what I want on the flyer. If you have any questions please do not hesitate to ask.
I have refined the design brief overnight, after receiving some feedback, please refer to newly uploaded file for this morning. I am hoping it makes things clearer and easier.
Industry/Entity Type
Small Business

```html
<!DOCTYPE html>
<html lang="en">
<head>
<meta charset="utf-8">
<title>Byte Harbor — Computer Repair Flyer</title>
<link rel="stylesheet" href="https://fonts.googleapis.com/css2?family=Bitter:wght@400&family=Source+Sans+3:wght@400;700&display=swap">
<style>
  :root {
    --paper: #ffffff;
    --stage: #ececec;
    --red: #e8332a;
    --ink: #1f1f1f;
    --label: #3f3f3f;
    --brand-blue: #2b5c9e;
    --swoosh-pink: #f3b9b4;
    --swoosh-blue: #bccde0;
    --photo-light: #d9dde2;
    --photo-dark: #2e3138;
  }
  html, body {
    margin: 0;
    padding: 0;
    width: 1200px;
    height: 798px;
    overflow: hidden;
    background: var(--stage);
  }
  .flyer {
    position: relative;
    width: 1200px;
    height: 798px;
    background: var(--paper);
    overflow: hidden;
    font-family: "Source Sans 3", "Helvetica Neue", Arial, sans-serif;
  }
  .swooshes {
    position: absolute;
    inset: 0;
  }
  .service {
    position: absolute;
    width: 140px;
    text-align: center;
    color: var(--label);
    font-size: 17px;
    line-height: 1.12;
  }
  .service svg {
    display: block;
    margin: 0 auto 14px;
  }
  .brand {
    position: absolute;
    right: 30px;
    top: 52px;
    display: flex;
    align-items: center;
    gap: 14px;
  }
  .brand-dot {
    width: 40px;
    height: 40px;
    border-radius: 50%;
    background: var(--red);
  }
  .brand-name {
    font-weight: 700;
    font-size: 54px;
    letter-spacing: 1px;
    color: var(--brand-blue);
    text-transform: uppercase;
    line-height: 1;
  }
  .headline {
    position: absolute;
    right: 30px;
    top: 144px;
    margin: 0;
    text-align: right;
    font-family: "Bitter", Georgia, serif;
    font-weight: 400;
    font-size: 59px;
    line-height: 73px;
    color: var(--ink);
  }
  .portrait {
    position: absolute;
    left: 330px;
    top: 150px;
    width: 560px;
    height: 648px;
    border-radius: 220px 220px 0 0;
    background: linear-gradient(180deg, var(--photo-light) 0%, #8a8f98 30%, var(--photo-dark) 70%);
  }
  .offers {
    position: absolute;
    right: 30px;
    top: 512px;
    margin: 0;
    padding: 0;
    list-style: none;
    text-align: right;
    color: var(--ink);
    font-size: 23.5px;
    line-height: 33px;
  }
  .offers li { margin-bottom: 11px; }
  .offers .pointer {
    display: inline-block;
    width: 14px;
    height: 18px;
    margin-right: 8px;
    vertical-align: -1px;
  }
</style>
</head>
<body>
<main class="flyer">
  <svg class="swooshes" width="1200" height="798" viewBox="0 0 1200 798" aria-hidden="true">
    <path d="M0 250 C 120 120, 260 40, 420 0 L 470 0 C 300 50, 150 150, 0 300 Z" fill="var(--swoosh-blue)" opacity="0.7"/>
    <path d="M0 560 C 90 330, 300 110, 560 0 L 620 0 C 350 130, 150 330, 0 660 Z" fill="var(--swoosh-pink)" opacity="0.8"/>
    <path d="M60 798 C 40 650, 120 480, 300 300 L 330 320 C 170 500, 100 650, 120 798 Z" fill="var(--swoosh-pink)" opacity="0.55"/>
    <path d="M580 120 C 760 60, 1000 40, 1200 20 L 1200 0 L 1080 0 C 900 30, 740 70, 580 120 Z" fill="var(--swoosh-blue)" opacity="0.8"/>
    <path d="M1200 300 C 1120 520, 980 690, 800 798 L 880 798 C 1040 690, 1160 540, 1200 420 Z" fill="var(--swoosh-blue)" opacity="0.75"/>
    <path d="M1200 620 C 1100 700, 1000 760, 920 798 L 980 798 C 1060 770, 1140 730, 1200 690 Z" fill="var(--swoosh-pink)" opacity="0.7"/>
  </svg>

  <div class="service" style="left:29px; top:40px;">
    <svg width="70" height="60" viewBox="0 0 70 60" aria-hidden="true">
      <rect x="8" y="6" width="50" height="34" rx="3" fill="none" stroke="var(--red)" stroke-width="5"/>
      <rect x="0" y="44" width="66" height="8" rx="3" fill="var(--red)"/>
      <path d="M40 4 l22 18 -6 6 -22 -18 z" fill="var(--red)"/>
      <path d="M20 14 l0 14 4 -4 4 7 3 -2 -4 -7 6 0 z" fill="var(--red)"/>
    </svg>
    Computer Repair, Service, Install And Upgrade
  </div>
  <div class="service" style="left:171px; top:40px;">
    <svg width="70" height="60" viewBox="0 0 70 60" aria-hidden="true">
      <rect x="20" y="2" width="30" height="20" rx="3" fill="none" stroke="var(--red)" stroke-width="4"/>
      <path d="M27 9h16M27 15h16" stroke="var(--red)" stroke-width="3"/>
      <path d="M35 22v10M10 32h50M10 32v8M35 32v8M60 32v8" stroke="var(--red)" stroke-width="4" fill="none"/>
      <circle cx="10" cy="49" r="9" fill="var(--red)"/>
      <circle cx="35" cy="49" r="9" fill="var(--red)"/>
      <circle cx="60" cy="49" r="9" fill="var(--red)"/>
    </svg>
    Setting Up Secure Networks
  </div>

  <div class="service" style="left:29px; top:248px;">
    <svg width="70" height="60" viewBox="0 0 70 60" aria-hidden="true">
      <rect x="6" y="4" width="40" height="28" rx="2" fill="var(--red)"/>
      <path d="M6 6 l20 16 20 -16" stroke="#fff" stroke-width="3" fill="none"/>
      <circle cx="42" cy="36" r="18" fill="none" stroke="var(--red)" stroke-width="5"/>
      <circle cx="42" cy="36" r="7" fill="none" stroke="var(--red)" stroke-width="4"/>
    </svg>
    Internet and Email Setup
  </div>
  <div class="service" style="left:171px; top:248px;">
    <svg width="70" height="60" viewBox="0 0 70 60" aria-hidden="true">
      <path d="M16 44 a12 12 0 0 1 2 -24 a16 16 0 0 1 30 -4 a13 13 0 0 1 8 26" fill="none" stroke="var(--red)" stroke-width="5"/>
      <path d="M18 30 l10 -8 v5 h14 v6 h-14 v5 z" fill="var(--red)"/>
      <path d="M62 46 l-10 8 v-5 h-14 v-6 h14 v-5 z" fill="var(--red)"/>
    </svg>
    Data Backup and Recovery
  </div>

  <div class="service" style="left:29px; top:444px;">
    <svg width="70" height="60" viewBox="0 0 70 60" aria-hidden="true">
      <rect x="4" y="2" width="62" height="46" rx="5" fill="none" stroke="var(--red)" stroke-width="4"/>
      <path d="M28 58 v-30 a4 4 0 0 1 8 0 v14 l12 2 a4 4 0 0 1 3 5 l-3 9" fill="none" stroke="var(--red)" stroke-width="4"/>
    </svg>
    Setting up New Hardware
  </div>
  <div class="service" style="left:171px; top:444px;">
    <svg width="84" height="60" viewBox="0 0 84 60" aria-hidden="true">
      <rect x="2" y="12" width="9" height="9" fill="var(--red)"/>
      <rect x="15" y="12" width="9" height="9" fill="var(--red)"/>
      <rect x="28" y="12" width="9" height="9" fill="var(--red)"/>
      <rect x="41" y="12" width="9" height="9" fill="var(--red)"/>
      <rect x="54" y="12" width="9" height="9" fill="none" stroke="var(--red)" stroke-width="2"/>
      <rect x="67" y="12" width="9" height="9" fill="none" stroke="var(--red)" stroke-width="2"/>
      <path d="M44 26 v28 l7 -7 6 11 5 -3 -6 -11 10 0 z" fill="var(--red)"/>
    </svg>
    Software Install And Configuration
  </div>

  <div class="service" style="left:29px; top:626px;">
    <svg width="70" height="60" viewBox="0 0 70 60" aria-hidden="true">
      <path d="M35 14 a14 14 0 0 1 8 26 v6 h-16 v-6 a14 14 0 0 1 8 -26 z" fill="var(--red)"/>
      <rect x="27" y="49" width="16" height="4" fill="var(--red)"/>
      <rect x="29" y="55" width="12" height="4" fill="var(--red)"/>
      <path d="M35 2v7M14 10l5 5M56 10l-5 5M6 28h7M57 28h7" stroke="var(--red)" stroke-width="3"/>
    </svg>
    Software Tricks, Tips and Tutorials
  </div>
  <div class="service" style="left:171px; top:626px;">
    <svg width="70" height="60" viewBox="0 0 70 60" aria-hidden="true">
      <path d="M16 30 a19 19 0 0 1 38 0" fill="none" stroke="var(--red)" stroke-width="4"/>
      <rect x="11" y="26" width="9" height="14" rx="3" fill="var(--red)"/>
      <rect x="50" y="26" width="9" height="14" rx="3" fill="var(--red)"/>
      <path d="M54 40 q0 8 -12 8" fill="none" stroke="var(--red)" stroke-width="3"/>
      <path d="M10 60 q0 -12 25 -12 q25 0 25 12 z" fill="var(--red)"/>
    </svg>
    Onsite and Remote Support Available
  </div>

  <div class="portrait" role="img" aria-label="Photo of a smiling technician in a dark suit holding an open white laptop"></div>

  <div class="brand">
    <span class="brand-dot" aria-hidden="true"></span>
    <span class="brand-name">Byte Harbor</span>
  </div>

  <h1 class="headline">Computer Repair<br>You Can<br>Depend On</h1>

  <ul class="offers">
    <li>
      <svg class="pointer" viewBox="0 0 14 18" aria-hidden="true"><path d="M1 1 v15 l4 -4 3 6 3 -1.5 -3 -6 5 0 z" fill="var(--red)"/></svg>$40 Per Hour Specific Job,<br>Or Am Happy To Bundle,<br>Provide Flexible Pricing<br>For More Complex Tasks
    </li>
    <li>
      <svg class="pointer" viewBox="0 0 14 18" aria-hidden="true"><path d="M1 1 v15 l4 -4 3 6 3 -1.5 -3 -6 5 0 z" fill="var(--red)"/></svg>No Call Out Fee
    </li>
    <li>
      <svg class="pointer" viewBox="0 0 14 18" aria-hidden="true"><path d="M1 1 v15 l4 -4 3 6 3 -1.5 -3 -6 5 0 z" fill="var(--red)"/></svg>Friendly, Hassle Free, Independent<br>Advice And Recommendations Given
    </li>
  </ul>
</main>
</body>
</html>
```